Business card design for holistic health care clinic

We need a double-sided business card design for our holistic health care clinic that integrates our logo design and also its color scheme. My business is called Valmira. It is an integrative medicine clinic. You have already done the logo for me. Please ensure an elegant and upscale design that is not cluttered, but still has all the necessary information (please see below for details).

Target Market(s)

Wellness, fitness, rehabilitation for educated, well-traveled open-minded clients who are focused on natural, organic, balanced and preventive healthcare and lifestyle.

Industry/Entity Type

Medical

Contact Information for Business Card

Modern, clean.

Number of Pages Required

1 page

Font styles to use
Serif
Sans Serif

Colors

Designer to choose colors to be used in the design.

Requirements
Must have
• Logo on one side, all other information on the other side.
• Other information should include:
• Tobias Wrenfeld - DOE, CPT, LMT
• 4100 East Marrow Drive
• Austin, TX 78119
• 512 555 0148
• 818 555 0192
• info@ValmiraHealth.example
• t.wrenfeld@ValmiraHealth.example
Nice to have
• Darker background on front - but not totally black - shaded/dark gray.

```html
<!DOCTYPE html>
<html lang="en">
<head>
<meta charset="utf-8">
<title>Valmira Business Card</title>
<link href="https://fonts.googleapis.com/css2?family=Nunito:wght@700&family=Roboto:ital,wght@0,400;1,500&family=Roboto+Condensed:wght@400;700&display=swap" rel="stylesheet">
<style>
  :root {
    --page: #262626;
    --brand-blue: #0a93d1;
    --card-dark: #2c2c2e;
    --text-light: #f2f2f2;
    --white: #ffffff;
  }
  * { margin: 0; padding: 0; box-sizing: border-box; }
  html, body { width: 1200px; height: 960px; overflow: hidden; }
  body { background: var(--page); position: relative; font-family: "Roboto", Arial, sans-serif; }

  .card {
    position: absolute;
    left: 320px;
    width: 600px;
    border-radius: 18px;
  }
  .card-front {
    top: 104px;
    height: 352px;
    background: var(--brand-blue);
  }
  .front-tagline {
    position: absolute;
    top: 58px; left: 0; right: 0;
    text-align: center;
    color: var(--white);
    font-style: italic;
    font-weight: 500;
    font-size: 17px;
  }
  .front-wordmark {
    position: absolute;
    top: 170px; left: 0; right: 0;
    text-align: center;
    color: var(--white);
    font-family: "Nunito", Arial, sans-serif;
    font-weight: 700;
    font-size: 72px;
    letter-spacing: 6px;
    text-transform: uppercase;
  }

  .card-back {
    top: 493px;
    height: 342px;
    background: var(--card-dark);
  }
  .back-wordmark {
    position: absolute;
    left: 37px; top: 60px;
    color: var(--brand-blue);
    font-family: "Nunito", Arial, sans-serif;
    font-weight: 700;
    font-size: 52px;
    letter-spacing: 1px;
    text-transform: uppercase;
    line-height: 1;
  }
  .back-descriptor {
    position: absolute;
    left: 41px; top: 118px;
    color: var(--brand-blue);
    font-family: "Nunito", Arial, sans-serif;
    font-weight: 700;
    font-size: 15px;
  }
  .contact {
    position: absolute;
    right: 33px; top: 146px;
    text-align: right;
    color: var(--text-light);
    font-size: 14px;
  }
  .contact-name {
    font-family: "Roboto Condensed", Arial, sans-serif;
    font-weight: 700;
    font-size: 21px;
    color: var(--brand-blue);
    letter-spacing: 0.3px;
  }
  .contact-credentials { font-size: 12px; font-weight: 700; }
  .contact-address { margin-top: 12px; line-height: 19px; }
  .contact-lines { margin-top: 9px; list-style: none; line-height: 19.5px; }
  .contact-lines li { display: flex; justify-content: flex-end; align-items: center; gap: 6px; }
  .contact-lines svg { width: 13px; height: 13px; fill: var(--brand-blue); flex: none; }
</style>
</head>
<body>

<section class="card card-front">
  <p class="front-tagline">helping the body help itself</p>
  <p class="front-wordmark">Valmira</p>
</section>

<section class="card card-back">
  <p class="back-wordmark">Valmira</p>
  <p class="back-descriptor">Integrative Holistic Medicine</p>

  <div class="contact">
    <p class="contact-name">TOBIAS WRENFELD <span class="contact-credentials">- DOE, CPT, LMT</span></p>
    <p class="contact-address">4100 East Marrow Drive<br>Austin, TX 78119</p>
    <ul class="contact-lines">
      <li>512 555 0148
        <svg viewBox="0 0 24 24" aria-hidden="true"><path d="M6.6 10.8a15 15 0 0 0 6.6 6.6l2.2-2.2c.3-.3.7-.4 1-.2 1.1.4 2.3.6 3.6.6.6 0 1 .4 1 1V20c0 .6-.4 1-1 1A17 17 0 0 1 3 4c0-.6.4-1 1-1h3.5c.6 0 1 .4 1 1 0 1.3.2 2.5.6 3.6.1.3 0 .7-.2 1z"/></svg>
      </li>
      <li>818 555 0192
        <svg viewBox="0 0 24 24" aria-hidden="true"><path d="M7 1h10a2 2 0 0 1 2 2v18a2 2 0 0 1-2 2H7a2 2 0 0 1-2-2V3a2 2 0 0 1 2-2zm0 3v14h10V4zm5 15.5a1 1 0 1 0 0 2 1 1 0 0 0 0-2z"/></svg>
      </li>
      <li>t.wrenfeld@ValmiraHealth.example
        <svg viewBox="0 0 24 24" aria-hidden="true"><path d="M2 5h20v14H2zm2 2v.5l8 5 8-5V7l-8 5z"/></svg>
      </li>
      <li>www.ValmiraHealth.example
        <svg viewBox="0 0 24 24" aria-hidden="true"><circle cx="12" cy="12" r="10"/></svg>
      </li>
    </ul>
  </div>
</section>

</body>
</html>
```